TLK Electricial Contracting Services

Hi guys, after a design for my small electrical company, have logo design files to be incorporated into the layout, the basic concept is electrical contracting services for residential, commercial, industrial & data services, image is clean clear and strong,

Card format is to have a nice clean logo on front,with maybe the Residential – commercial – industrial - data, followed with licensed & insured, followed by contact details on backside of the card.

Target Market(s)

Residential, commercial, industrial sectors.

Industry/Entity Type

Electrical

Contact Information for Business Card

TLK logo,
Residential – commercial – industrial - data
REC: 61307
Email: tlk@vornamail.net.au
Phone: 0487 352 019

Requirements
Must have
• Clean & strong design.
Nice to have
• If possible, I would like the logo colours inverted so the text is orange and the background is black on the front of the card, then the backside of the card be the reverse colour
Should not have
• No Sparks, lightning bolts,

```html
<!DOCTYPE html>
<html lang="en">
<head>
<meta charset="utf-8">
<title>TLK Electricial Contracting Services – Business Card</title>
<link rel="stylesheet" href="https://fonts.googleapis.com/css2?family=Lato:wght@400;700;900&display=swap">
<style>
  :root {
    --backdrop: #e9e9e9;
    --card-light: #f7f7f7;
    --card-dark: #1f1e22;
    --ink: #1c1c1e;
    --ink-muted: #6a6a6a;
    --accent-orange: #f28a1e;
    --paper-white: #ffffff;
  }
  * { margin: 0; padding: 0; box-sizing: border-box; }
  html, body {
    width: 1200px;
    height: 900px;
    overflow: hidden;
    background: var(--backdrop);
    font-family: "Lato", Arial, sans-serif;
  }
  .canvas {
    position: relative;
    width: 1200px;
    height: 900px;
  }
  .card {
    position: absolute;
    top: 307px;
    width: 500px;
    height: 286px;
    border-radius: 2px;
    box-shadow: 0 6px 22px rgba(0, 0, 0, 0.12);
  }
  .card--details {
    left: 70px;
    background: var(--card-light);
    color: var(--ink);
  }
  .card--brand {
    left: 630px;
    background: var(--card-dark);
    color: var(--paper-white);
    display: flex;
    flex-direction: column;
    align-items: center;
    justify-content: center;
  }
  .holder {
    position: absolute;
    left: 34px;
    top: 34px;
  }
  .holder__name {
    font-size: 19px;
    font-weight: 700;
    letter-spacing: 0.2px;
  }
  .holder__role {
    margin-top: 3px;
    font-size: 12px;
    color: var(--ink-muted);
  }
  .contact {
    position: absolute;
    left: 34px;
    top: 112px;
    list-style: none;
    font-size: 13px;
    line-height: 1.3;
  }
  .contact__label {
    font-weight: 700;
    font-size: 12px;
  }
  .contact__value {
    margin-bottom: 3px;
    color: var(--ink);
  }
  .wordmark {
    display: flex;
    flex-direction: column;
    font-weight: 900;
    line-height: 1;
  }
  .wordmark__initials {
    font-size: 78px;
    letter-spacing: 2px;
  }
  .wordmark__name {
    margin-top: 4px;
    font-size: 15px;
    letter-spacing: 0.4px;
  }
  .card--details .wordmark {
    position: absolute;
    right: 34px;
    top: 120px;
    color: var(--ink);
  }
  .card--brand .wordmark {
    align-items: center;
    color: var(--accent-orange);
  }
  .services {
    margin-top: 20px;
    font-size: 11px;
    font-weight: 700;
    letter-spacing: 1.6px;
    text-transform: uppercase;
    color: var(--paper-white);
  }
  .credentials {
    margin-top: 7px;
    font-size: 11px;
    font-weight: 400;
    letter-spacing: 1.6px;
    text-transform: uppercase;
    color: var(--accent-orange);
  }
</style>
</head>
<body>
<main class="canvas">
  <section class="card card--details" aria-label="Business card, contact side">
    <div class="holder">
      <p class="holder__name">Daniel Hartley</p>
      <p class="holder__role">Managing Director</p>
    </div>
    <ul class="contact">
      <li class="contact__label">telephone</li>
      <li class="contact__value">0487 352 019</li>
      <li class="contact__label">email</li>
      <li class="contact__value">tlk@vornamail.net.au</li>
      <li class="contact__label">licence</li>
      <li class="contact__value">REC 61307</li>
    </ul>
    <div class="wordmark">
      <span class="wordmark__initials">TLK</span>
      <span class="wordmark__name">Tarlow Kent Electrical</span>
    </div>
  </section>

  <section class="card card--brand" aria-label="Business card, brand side">
    <div class="wordmark">
      <span class="wordmark__initials">TLK</span>
      <span class="wordmark__name">Tarlow Kent Electrical</span>
    </div>
    <p class="services">Residential – Commercial – Industrial – Data</p>
    <p class="credentials">Licensed &amp; Insured</p>
  </section>
</main>
</body>
</html>
```